Q + Public Adjusters Collective Business card

We need to get business card Design for our Company we are Public Adjusters in Chicago Illinois - i like to see good combination and elements from my Company Logo. as well To be an two side design
Updates

Target Market(s)

Home /Business owner Property Managers

Industry/Entity Type

Business

Contact Information for Business Card

to show the Element of our logo i will Like 3D

Font styles to use
Sans Serif

Requirements
Must have
• Logo and Element of the Logo in 3D
Nice to have
• Logo That we Provide 3D Same Colors or open for suggestions
Should not have
• unleare view -

```html
<!DOCTYPE html>
<html lang="en">
<head>
<meta charset="utf-8">
<title>Q + Public Adjusters Collective — Stationery</title>
<link rel="stylesheet" href="https://fonts.googleapis.com/css2?family=Lato:wght@400;700&display=swap">
<style>
  :root{
    --bg:#eeeff1;
    --paper:#ffffff;
    --navy:#1c2566;
    --navy-deep:#202348;
    --blue:#1f4fd6;
    --red:#c4161c;
    --ink:#2b2b2b;
    --muted:#5a5a5a;
  }
  *{box-sizing:border-box;margin:0;padding:0}
  html,body{width:1200px;height:795px;overflow:hidden;background:var(--bg);font-family:"Lato",sans-serif;color:var(--ink)}
  .canvas{position:relative;width:1200px;height:795px}
  .sheet{position:absolute;background:var(--paper);overflow:hidden}
  .brand{display:flex;align-items:center;gap:4px;color:var(--navy);font-weight:700;white-space:nowrap}
  .brand-dot{display:inline-block;border-radius:50%;background:var(--red);flex:none}
  .brand-stacked{flex-direction:column;gap:3px;text-align:center;white-space:normal}
  .accent-bar{position:absolute;left:0;bottom:0;width:100%;display:block}

  /* letterhead */
  .letterhead{left:292px;top:99px;width:293px;height:415px}
  .letterhead .brand{position:absolute;left:24px;top:30px;width:72px;font-size:6.5px;line-height:8px}
  .letterhead .brand-dot{width:12px;height:12px}
  .letterhead .contact{position:absolute;right:22px;top:24px;text-align:right;font-size:3.6px;line-height:5.6px;color:var(--muted)}
  .contact .gap{height:4px}
  .salutation{position:absolute;left:25px;top:101px;font-size:7px}
  .letter-body{position:absolute;left:25px;top:130px;width:243px;font-size:5.1px;line-height:9px;color:var(--muted);text-align:justify}
  .letter-body p+p{margin-top:9px}
  .signer{position:absolute;left:25px;top:294px;font-size:6.8px}
  .signer-role{position:absolute;left:25px;top:307px;font-size:4.2px;color:var(--muted)}
  .signature{position:absolute;left:18px;top:332px;width:72px;height:30px;background:linear-gradient(90deg,#f3f3f3,#e8e8e8)}

  /* folder */
  .folder{left:636px;top:80px;width:346px;height:437px;background:radial-gradient(ellipse 60% 45% at 55% 52%,#1d4fe0 0%,#1c3aa8 35%,var(--navy-deep) 100%)}
  .folder-spine{position:absolute;left:0;top:0;width:18px;height:100%;background:var(--red)}
  .folder .brand{position:absolute;left:18px;right:0;top:222px;justify-content:center;font-size:13px;color:#5f7ff0}
  .folder .brand-dot{width:11px;height:11px}

  /* business cards */
  .card{width:133px;height:76px;left:186px}
  .card-front{top:550px}
  .card-front .brand{position:absolute;left:6px;top:18px;width:62px;font-size:4.6px;line-height:5.6px}
  .card-front .brand-dot{width:10px;height:10px}
  .card-divider{position:absolute;left:74px;top:10px;width:0.6px;height:50px;background:#c9c9c9}
  .card-front .details{position:absolute;left:78px;top:12px;font-size:3.2px;line-height:4.7px;color:var(--muted)}
  .card-name{font-size:4.6px;font-weight:700;color:var(--navy);line-height:5px}
  .card-title{color:var(--red);font-weight:700;margin-bottom:3px}
  .card-back{top:647px;height:75px;background:radial-gradient(ellipse 55% 60% at 50% 40%,#1e4fd8 0%,#1c36a0 45%,var(--navy-deep) 100%)}
  .card-back .brand-dot{position:absolute;left:57px;top:19px;width:19px;height:19px;background:var(--red)}
  .card-back .url{position:absolute;left:0;width:100%;top:60px;text-align:center;font-size:3.6px;letter-spacing:.3px;color:#dfe6ff}

  /* envelopes */
  .envelope{top:562px;width:329px;height:156px}
  .envelope-front{left:353px}
  .envelope-front .brand{position:absolute;left:15px;top:14px;width:66px;align-items:flex-start;text-align:left;font-size:5.4px;line-height:6.6px}
  .envelope-front .brand-dot{width:11px;height:11px;margin-left:12px}
  .envelope-front .address{position:absolute;left:15px;top:52px;font-size:4.2px;line-height:6px;color:var(--muted)}
  .envelope-back{left:713px}
  .envelope-back svg{position:absolute;left:0;top:0}
</style>
</head>
<body>
<main class="canvas">

  <section class="sheet letterhead" aria-label="Letterhead">
    <div class="brand brand-stacked"><span class="brand-dot"></span>Q + Public Adjusters Collective</div>
    <div class="contact">
      <div>4120 Linden Court</div>
      <div>Marlow, Illinois 60999</div>
      <div class="gap"></div>
      <div>312 555 0148 ☎</div>
      <div>312 555 0172 ▯</div>
      <div>312 555 0193 ▬</div>
      <div>hello@qpacollective.com ✉</div>
      <div>www.qpacollective.com ●</div>
    </div>
    <div class="salutation">Dear Mr. Marsh,</div>
    <div class="letter-body">
      <p>We are writing to confirm that our team has completed the first review of your property claim. Our adjusters inspected the roof, the interior rooms and the water damage in the lower level, and every finding has been recorded with dated photos and notes. We will now prepare a full estimate of the loss and submit it to your insurer within the agreed period. Please keep all receipts for repairs and temporary housing, as these costs may be included in the settlement we request on your behalf.</p>
      <p>If you have questions about any step of the process, our office is open every weekday and we are glad to meet with you in person. Our team will call you next week to set a date for the second visit. Thank you for trusting us with your claim; we look forward to reaching a fair outcome together.</p>
    </div>
    <div class="signer">Evan Marsh</div>
    <div class="signer-role">Co-Founder &amp; CEO</div>
    <div class="signature" role="img" aria-label="Handwritten signature of Evan Marsh"></div>
    <svg class="accent-bar" width="293" height="7" viewBox="0 0 293 7" preserveAspectRatio="none">
      <defs><linearGradient id="barLetter" x1="0" x2="1"><stop offset="0" stop-color="#1c2566"/><stop offset=".6" stop-color="#1f4fd6"/><stop offset="1" stop-color="#1c2566"/></linearGradient></defs>
      <polygon points="0,0 231,0 228,7 0,7" fill="url(#barLetter)"/>
      <polygon points="233,0 293,0 293,7 230,7" fill="#c4161c"/>
    </svg>
  </section>

  <section class="sheet folder" aria-label="Presentation folder">
    <div class="folder-spine"></div>
    <div class="brand"><span class="brand-dot"></span>Q + Public Adjusters Collective</div>
  </section>

  <section class="sheet card card-front" aria-label="Business card front">
    <div class="brand brand-stacked"><span class="brand-dot"></span>Q + Public Adjusters Collective</div>
    <div class="card-divider"></div>
    <div class="details">
      <div class="card-name">LENA ORTIZ</div>
      <div class="card-title">CEO / Founder</div>
      <div>4120 Linden Court</div>
      <div>Marlow, Illinois 60999</div>
      <div>☎ 312 555 0148</div>
      <div>▯ 312 555 0172</div>
      <div>▬ 312 555 0193</div>
      <div>✉ hello@qpacollective.com</div>
      <div>● www.qpacollective.com</div>
    </div>
    <svg class="accent-bar" width="133" height="6" viewBox="0 0 133 6" preserveAspectRatio="none">
      <defs><linearGradient id="barCard" x1="0" x2="1"><stop offset="0" stop-color="#1c2566"/><stop offset=".6" stop-color="#1f4fd6"/><stop offset="1" stop-color="#1c2566"/></linearGradient></defs>
      <polygon points="0,0 88,0 86,6 0,6" fill="url(#barCard)"/>
      <polygon points="90,0 133,0 133,6 87,6" fill="#c4161c"/>
    </svg>
  </section>

  <section class="sheet card card-back" aria-label="Business card back">
    <span class="brand-dot"></span>
    <div class="url">www.qpacollective.com</div>
  </section>

  <section class="sheet envelope envelope-front" aria-label="Envelope front">
    <div class="brand brand-stacked"><span class="brand-dot"></span>Q + Public Adjusters Collective</div>
    <div class="address">
      <div>4120 Linden Court</div>
      <div>Marlow, Illinois 60999</div>
    </div>
    <svg class="accent-bar" width="329" height="7" viewBox="0 0 329 7" preserveAspectRatio="none">
      <defs><linearGradient id="barEnv" x1="0" x2="1"><stop offset="0" stop-color="#1c2566"/><stop offset=".6" stop-color="#1f4fd6"/><stop offset="1" stop-color="#1c2566"/></linearGradient></defs>
      <polygon points="0,0 262,0 259,7 0,7" fill="url(#barEnv)"/>
      <polygon points="264,0 329,0 329,7 261,7" fill="#c4161c"/>
    </svg>
  </section>

  <section class="sheet envelope envelope-back" aria-label="Envelope back">
    <svg width="329" height="156" viewBox="0 0 329 156">
      <polyline points="0,0 4,34 18,38 311,38 325,34 329,0" fill="none" stroke="#e2e3e6" stroke-width="1"/>
    </svg>
  </section>

</main>
</body>
</html>
```